A4 Single Sided Brochure Folder Design Technical Company

We are a technical company based in the UK, working worldwide for Power Distribution companies.

We have technical literature and need a folder to present these in. The design should be very simple and clean using our logo and "Innovative Utility Solutions"

Our website kestrome.com gives and idea of the business but don't follow the look of the website as we will be redoing shortly.

• Logo and Strap Line
• Clean, easy to print and timeless
• Shouldn't be fashionable, we certainly aren't

```html
<!DOCTYPE html>
<html lang="en">
<head>
<meta charset="UTF-8">
<title>Kestrome – Presentation Folder</title>
<link href="https://fonts.googleapis.com/css2?family=Montserrat:wght@300;400&display=swap" rel="stylesheet">
<style>
  :root {
    --magenta: #b52a8c;
    --magenta-deep: #a02479;
    --paper: #ffffff;
    --ink-grey: #9c9c9c;
    --ink-soft: #a8a8a8;
    --backdrop-light: #f2f2f2;
    --backdrop-dark: #c9c9c9;
  }
  * { margin: 0; padding: 0; box-sizing: border-box; }
  html, body {
    width: 1200px;
    height: 750px;
    overflow: hidden;
  }
  body {
    background: radial-gradient(ellipse at 45% 45%, var(--backdrop-light) 0%, #dedede 60%, var(--backdrop-dark) 100%);
    font-family: "Montserrat", sans-serif;
    position: relative;
  }
  .folder-spread {
    position: absolute;
    left: 148px;
    top: 55px;
    width: 904px;
    height: 640px;
    display: flex;
    box-shadow: 0 18px 40px rgba(0,0,0,0.18);
  }
  .folder-panel {
    position: relative;
    width: 452px;
    height: 640px;
    background: var(--paper);
    overflow: hidden;
  }
  .folder-panel--back { border-right: 1px solid rgba(0,0,0,0.06); }
  .panel-band {
    position: absolute;
    inset: 0;
    width: 100%;
    height: 100%;
  }
  .brand-name {
    position: absolute;
    right: 56px;
    top: 340px;
    color: var(--paper);
    font-weight: 300;
    font-size: 60px;
    letter-spacing: 2px;
    line-height: 1;
  }
  .strap-line {
    position: absolute;
    left: 0;
    right: 0;
    top: 500px;
    text-align: center;
    color: var(--ink-grey);
    font-weight: 300;
    font-size: 19px;
    letter-spacing: 0.5px;
  }
  .web-address {
    position: absolute;
    left: 0;
    right: 0;
    top: 540px;
    text-align: center;
    color: var(--ink-soft);
    font-weight: 400;
    font-size: 11px;
    letter-spacing: 0.5px;
  }
</style>
</head>
<body>
  <main class="folder-spread">
    <section class="folder-panel folder-panel--back">
      <svg class="panel-band" viewBox="0 0 452 640" preserveAspectRatio="none" aria-hidden="true">
        <path d="M0,0 H452 V420 Q226,470 0,462 Z" fill="var(--magenta-deep)"/>
      </svg>
      <p class="web-address">www.kestrome.com</p>
    </section>
    <section class="folder-panel folder-panel--front">
      <svg class="panel-band" viewBox="0 0 452 640" preserveAspectRatio="none" aria-hidden="true">
        <path d="M0,0 H452 V400 Q226,470 0,452 Z" fill="var(--magenta)"/>
      </svg>
      <h1 class="brand-name">Kestrome</h1>
      <p class="strap-line">Innovative Utility Solutions</p>
    </section>
  </main>
</body>
</html>
```